Business card design for holistic health care clinic

We need a double-sided business card design for our holistic health care clinic that integrates our logo design and also its color scheme. My business is called Valmira. It is an integrative medicine clinic. You have already done the logo for me. Please ensure an elegant and upscale design that is not cluttered, but still has all the necessary information (please see below for details).

Target Market(s)

Wellness, fitness, rehabilitation for educated, well-traveled open-minded clients who are focused on natural, organic, balanced and preventive healthcare and lifestyle.

Industry/Entity Type

Medical

Contact Information for Business Card

Modern, clean.

Number of Pages Required

1 page

Font styles to use
Serif
Sans Serif

Colors

Designer to choose colors to be used in the design.

Requirements
Must have
• Logo on one side, all other information on the other side.
• Other information should include:
• Tobias Wrenfeld - DOE, CPT, LMT
• 4100 East Marrow Drive
• Austin, TX 78119
• 512 555 0148
• 818 555 0192
• info@ValmiraHealth.example
• t.wrenfeld@ValmiraHealth.example
Nice to have
• Darker background on front - but not totally black - shaded/dark gray.

```html
<!DOCTYPE html>
<html lang="en">
<head>
<meta charset="utf-8">
<title>Valmira Business Card</title>
<link rel="stylesheet" href="https://fonts.googleapis.com/css2?family=Montserrat:wght@500;700&family=Quicksand:wght@500;600&display=swap">
<style>
  :root {
    --backdrop: #2e2926;
    --card: #343435;
    --card-edge: #2a2a2b;
    --brand-blue: #1b8fd2;
    --line-blue: #1a7fbd;
  }
  * { box-sizing: border-box; margin: 0; padding: 0; }
  html, body { width: 1200px; height: 780px; overflow: hidden; }
  body {
    background: var(--backdrop);
    position: relative;
    font-family: "Quicksand", sans-serif;
  }
  .card {
    position: absolute;
    width: 520px;
    height: 298px;
    background: var(--card);
    border-radius: 3px;
    box-shadow: 0 14px 30px rgba(0,0,0,.45), 0 0 0 1px var(--card-edge);
    overflow: hidden;
  }
  .card--front { left: 70px; top: 110px; }
  .card--back { left: 610px; top: 372px; }

  .brand {
    position: absolute;
    left: 0; right: 0; top: 102px;
    text-align: center;
    color: var(--brand-blue);
  }
  .brand__name {
    font-family: "Montserrat", sans-serif;
    font-weight: 700;
    font-size: 56px;
    letter-spacing: 1px;
    line-height: 1;
    text-transform: uppercase;
  }
  .brand__tagline {
    font-family: "Montserrat", sans-serif;
    font-weight: 500;
    font-size: 15px;
    margin-top: 8px;
    letter-spacing: .3px;
  }

  .name-marker {
    position: absolute;
    left: -15px; top: 108px;
    width: 30px; height: 30px;
    border-radius: 50%;
    background: var(--brand-blue);
  }
  .person {
    position: absolute;
    left: 34px; top: 106px;
    color: var(--brand-blue);
  }
  .person__name {
    font-family: "Montserrat", sans-serif;
    font-weight: 700;
    font-size: 15px;
    text-transform: uppercase;
    letter-spacing: .3px;
  }
  .person__credentials {
    font-size: 12px;
    font-weight: 500;
    margin-top: 2px;
  }
  .rule {
    position: absolute;
    left: 34px; right: 30px; top: 160px;
    height: 1px;
    background: var(--line-blue);
  }
  .contacts {
    position: absolute;
    left: 24px; right: 18px; top: 182px;
    display: flex;
    align-items: stretch;
    color: var(--brand-blue);
    font-size: 10.5px;
    font-weight: 600;
  }
  .contacts__group {
    display: flex;
    flex-direction: column;
    justify-content: center;
    gap: 7px;
    padding: 0 10px;
  }
  .contacts__group + .contacts__group { border-left: 1px solid var(--line-blue); }
  .contact-item { display: flex; align-items: center; gap: 5px; white-space: nowrap; }
  .contact-item svg { width: 13px; height: 13px; flex: none; }
  .address { line-height: 1.4; font-size: 11px; }
</style>
</head>
<body>
  <section class="card card--front" aria-label="Card front">
    <div class="brand">
      <div class="brand__name">Valmira</div>
      <div class="brand__tagline">Integrative Holistic Medicine</div>
    </div>
  </section>

  <section class="card card--back" aria-label="Card back">
    <span class="name-marker"></span>
    <div class="person">
      <div class="person__name">Tobias Wrenfeld</div>
      <div class="person__credentials">DOE, CPT, LMT</div>
    </div>
    <div class="rule"></div>
    <div class="contacts">
      <div class="contacts__group">
        <div class="contact-item">
          <svg viewBox="0 0 14 14" fill="none" stroke="currentColor" stroke-width="1.1"><circle cx="7" cy="7" r="6.3"/><rect x="4.8" y="3.4" width="4.4" height="7.2" rx=".7"/></svg>
          512 555 0148
        </div>
        <div class="contact-item">
          <svg viewBox="0 0 14 14" fill="none" stroke="currentColor" stroke-width="1.1"><circle cx="7" cy="7" r="6.3"/><path d="M4.6 3.8c-.6.6-.5 2 .9 3.6s3 2 3.7 1.3l.6-.6-1.4-1.2-.7.5c-.6-.3-1.3-1-1.6-1.6l.5-.7L5.4 3.4z" fill="currentColor" stroke="none"/></svg>
          818 555 0192
        </div>
      </div>
      <div class="contacts__group">
        <div class="contact-item">
          <svg viewBox="0 0 14 14" fill="none" stroke="currentColor" stroke-width="1.1"><circle cx="7" cy="7" r="6.3"/><rect x="3.6" y="4.6" width="6.8" height="4.8"/><path d="M3.6 4.6 7 7.4l3.4-2.8"/></svg>
          info@ValmiraHealth.example
        </div>
        <div class="contact-item">
          <svg viewBox="0 0 14 14" fill="none" stroke="currentColor" stroke-width="1.1"><circle cx="7" cy="7" r="6.3"/><rect x="3.6" y="4.6" width="6.8" height="4.8"/><path d="M3.6 4.6 7 7.4l3.4-2.8"/></svg>
          t.wrenfeld@ValmiraHealth.example
        </div>
      </div>
      <div class="contacts__group address">
        <div>4100 East Marrow Drive</div>
        <div>Austin, TX 78119</div>
      </div>
    </div>
  </section>
</body>
</html>
```